Personal Training Business at home (Fern Vitality & Health)

My business name will be Fern Vitality & Health and will be training people with special needs (Asthma, Diabetes, Obesity, Rehab, Sports Performance) for all ages. It will be set indoor and outdoor for all types of weather conditions. I,m also doing Pilates group classes as well in a Japanese garden setting.I will be working alone so the groups will be small and the client has a high quality of service. I just need something very basic to start with then as the business expands I can edit it to it,s growth.

Target Market(s)

Target special population persons with dysfunctions injuries, metabolic/cardio-respiratory conditions, sports performance and more also healthy food choices.

Industry/Entity Type

Business

Number of Pages Required

3 page

Font styles to use
Serif

Colors
f78f20
ffffff
474747
cbcbcb
abd036

Requirements
Must have
• The website must have accessibility for change, to be able to link on other networks like my own YouTube videos. A basic lay out so I can fill in the pages and ad more as I expand the business. The logo to have the A for Fern to be an image of a man shaped as the letter A with his arms extended out/up. Private Facility and must ring for appointment to enter premises.
Nice to have
• The Image I want to have in my studio is for people to be serious about training & health choices. I want them to be able to train in a comfortable environment and free of air conditioned concrete rooms with machines. My home is converted to a Organic feature and outdoor/indoor training facility that my clients & I can share the natural freedom of training in the elements. My client have special needs and need extra care, they are people with injuries, metabolic/cardio-respiratory condition, asthmatics & more they need to be screened and tested for the condition that they suffer from and together with there allied professional we work together to treat them with the up most care for maximum results. This is what I want to target I long term client with real Goals on there mind and not some pipe dream.
Should not have
• Not to be portray as a Gym with machines and clients that only care about image.

```html
<!DOCTYPE html>
<html lang="en">
<head>
<meta charset="utf-8">
<title>Fern Fitness</title>
<link rel="stylesheet" href="https://fonts.googleapis.com/css2?family=Montserrat:wght@400;600;700&family=Open+Sans:ital,wght@0,400;0,600;1,400&display=swap">
<style>
:root{
  --orange:#f78f20;
  --green:#abd036;
  --ink:#474747;
  --grey:#cbcbcb;
  --white:#ffffff;
  --pale:#f4f4f4;
  --dark:#2f2f2f;
  --darker:#232323;
  --wood:#3a3431;
}
*{box-sizing:border-box;margin:0;padding:0}
html,body{width:1200px;height:2956px;overflow:hidden}
body{position:relative;font-family:"Open Sans",Arial,sans-serif;color:var(--ink);background:var(--white)}
.abs{position:absolute}
h1,h2,h3,.brand,.nav,.btn{font-family:"Montserrat",Arial,sans-serif}
.accent{color:var(--orange)}

/* header */
.topline{left:0;top:0;width:1200px;height:5px;background:var(--orange)}
.brand{left:98px;top:82px;font-size:22px;font-weight:700;color:var(--ink);letter-spacing:.5px;display:flex;align-items:center;gap:10px}
.brand .dot{width:14px;height:14px;border-radius:50%;background:var(--green)}
.brand b{color:var(--orange)}
.phone{right:98px;top:32px;display:flex;align-items:center;gap:10px;font-family:"Montserrat",sans-serif;font-weight:600;font-size:17px;color:var(--ink)}
.nav{right:98px;top:80px;display:flex;gap:38px;font-size:14px;color:var(--ink)}
.nav .current{color:var(--orange);border-bottom:2px solid var(--green);padding-bottom:8px}

/* hero */
.hero{left:0;top:136px;width:1200px;height:544px;background:radial-gradient(ellipse at 50% 40%,#5d6b50 0%,#3e3a33 55%,#2b2522 100%)}
.hero h1{position:absolute;left:0;top:278px;width:1200px;text-align:center;color:var(--white);font-size:33px;font-weight:700;letter-spacing:.5px}
.hero .arrow{position:absolute;top:250px}

/* welcome */
.welcome{left:0;top:680px;width:1200px;height:285px;text-align:center}
.welcome h2{margin-top:52px;font-size:28px;font-weight:600}
.welcome p{width:840px;margin:12px auto 0;font-size:12.5px;line-height:20px;color:#6a6a6a}
.btn{display:inline-flex;align-items:center;justify-content:center;height:52px;font-size:15px;color:var(--white);background:var(--green)}
.btn-outline{background:var(--white);color:var(--orange);border:1px solid var(--orange)}
.welcome .btns{margin-top:20px;display:flex;justify-content:center;gap:16px}

/* services */
.services{left:0;top:965px;width:1200px;height:440px;background:var(--pale)}
.services h2{position:absolute;top:52px;width:1200px;text-align:center;font-size:28px;font-weight:600}
.service{position:absolute;top:125px;width:240px;text-align:center}
.service .ring{width:134px;height:134px;margin:0 auto;border-radius:50%;border:2px solid var(--grey);background:var(--white);padding:6px}
.service .ring div{width:100%;height:100%;border-radius:50%;background:radial-gradient(circle at 40% 35%,#f5a04a,var(--orange))}
.service.green .ring div{background:radial-gradient(circle at 40% 35%,#c3e060,var(--green))}
.service h3{margin-top:14px;font-size:13.5px;font-weight:600;line-height:18px;color:#333}
.service p{margin-top:4px;font-size:12.5px;line-height:19px;color:#666}
.service a{display:block;margin-top:12px;font-size:12px;color:var(--orange);text-decoration:none}
.side-arrow{position:absolute;top:262px;width:24px;height:24px;border-radius:50%;background:#d6d6d6}

/* about */
.about-photo{left:98px;top:1458px;width:252px;height:322px;border:4px solid var(--white);box-shadow:0 0 0 1px var(--grey);background:linear-gradient(160deg,#6d8f5a,#4b5d4a 55%,#2f3d5e)}
.about{left:432px;top:1452px;width:670px}
.about h2{font-size:28px;font-weight:600}
.about p{margin-top:12px;font-size:12.5px;line-height:21.5px;color:#555}
.about .btn{width:192px;margin-top:18px}

/* group */
.group{left:0;top:1848px;width:1200px;height:427px;background:linear-gradient(180deg,#3b3532,#2a2624)}
.group h2{position:absolute;left:98px;top:62px;font-size:30px;font-weight:600;color:var(--white)}
.group p{position:absolute;left:102px;top:110px;width:455px;font-size:12.5px;line-height:23.5px;color:#eee}
.group .btn{position:absolute;left:102px;top:312px;width:192px}
.video{position:absolute;left:604px;top:64px;width:496px;height:300px;background:var(--white);padding:14px}
.video .screen{width:100%;height:232px;background:linear-gradient(160deg,#5f7a4c,#8a6a45 55%,#a77a4f)}
.video .bar{display:flex;align-items:center;gap:10px;height:30px;padding:0 8px;background:#1e1e1e;font-size:9px;color:#ccc}

/* testimonials */
.testi h2{position:absolute;left:0;top:2337px;width:1200px;text-align:center;font-size:28px;font-weight:600}
.testi-photo{left:158px;top:2394px;width:192px;height:192px;border-radius:50%;border:3px solid var(--grey);background:linear-gradient(180deg,#f0ece6,#d8d2ca)}
.quote{left:450px;top:2420px;width:560px;font-size:12.5px;line-height:22px;font-style:italic;color:#777}
.qmark{font-family:Georgia,serif;font-size:56px;color:var(--grey)}
.testi-name{left:450px;top:2528px;font-size:12px;font-weight:600;color:var(--green);letter-spacing:.5px}
.testi-role{left:450px;top:2550px;font-size:12px;color:#333}

/* footer */
.footer{left:0;top:2648px;width:1200px;height:257px;background:var(--dark);color:#ddd}
.footer .brand{left:128px;top:150px;color:var(--white);font-size:21px}
.footer h3{font-size:19px;font-weight:400;color:var(--white)}
.hours h4{font-family:"Montserrat",sans-serif;font-size:13px;font-weight:600;color:var(--white);margin:10px 0 8px}
.hours li{list-style:none;font-size:12px;line-height:28px;color:#ddd}
.hours li::before{content:"›";margin-right:10px}
.contact li{list-style:none;display:flex;align-items:center;gap:14px;font-size:11px;line-height:15px;margin-top:14px}
.contact .big{font-family:"Montserrat",sans-serif;font-size:17px;font-weight:600;color:var(--white)}
.bottom{left:0;top:2905px;width:1200px;height:51px;background:var(--darker);color:#ccc;font-size:12px}
.social{position:absolute;top:12px;display:flex;gap:6px}
.social span{width:28px;height:28px;border-radius:50%;background:#3a6ec0}
</style>
</head>
<body>

<header>
  <div class="abs topline"></div>
  <div class="abs brand"><span class="dot"></span><span><b>FERN</b> FITNESS</span></div>
  <div class="abs phone">
    <svg width="28" height="28" viewBox="0 0 28 28"><circle cx="14" cy="14" r="12.5" fill="none" stroke="#abd036" stroke-width="2"/><path d="M10 8.5l2.2-.5 1.3 3-1.5 1.2a8 8 0 0 0 3.8 3.8l1.2-1.5 3 1.3-.5 2.2c-5 .6-10.1-4.5-9.5-9.5z" fill="#abd036"/></svg>
    0400 123 456
  </div>
  <nav class="abs nav">
    <span class="current">Home</span><span>About us</span><span>Why train with us</span><span>Training services</span><span>Contact us</span>
  </nav>
</header>

<section class="abs hero" role="img" aria-label="Japanese garden with bonsai trees on wooden stands along a timber fence">
  <svg class="arrow" style="left:40px" width="20" height="56" viewBox="0 0 20 56"><path d="M18 2L3 28l15 26" fill="none" stroke="#ffffff" stroke-opacity=".6" stroke-width="2"/></svg>
  <svg class="arrow" style="right:40px" width="20" height="56" viewBox="0 0 20 56"><path d="M2 2l15 26L2 54" fill="none" stroke="#ffffff" stroke-opacity=".6" stroke-width="2"/></svg>
  <h1>ORGANIC PILATES EXPERIENCE</h1>
</section>

<section class="abs welcome">
  <h2>WELCOME TO <span class="accent">FERN</span> FITNESS</h2>
  <p>All my life I have been looking for a place that I can train in a comfortable and natural environment instead been surrounded by concrete walls &amp; floors, what I am offering in my studio gym is a natural organic style of training that clients can feel whatit's like to be outside in the elements. This is something that you can come feel &amp; enjoy the pleasure of training in the outdoors and still accomplishing your goals.</p>
  <div class="btns">
    <span class="btn" style="width:190px">Meet our Team</span>
    <span class="btn btn-outline" style="width:192px">View more info</span>
  </div>
</section>

<section class="abs services">
  <h2><span class="accent">TRAINING</span> SERVICES</h2>
  <span class="side-arrow" style="left:38px"></span>
  <span class="side-arrow" style="right:38px"></span>
  <div class="service green" style="left:102px">
    <div class="ring"><div role="img" aria-label="Icon of a person doing a floor exercise"></div></div>
    <h3>PERSONAL TRAINING ONE<br>ON ONE</h3>
    <p>The business is constantly staying<br>intouch with newest concepts</p>
    <a>Read more &gt;&gt;</a>
  </div>
  <div class="service" style="left:358px">
    <div class="ring"><div role="img" aria-label="Icon of a person skipping rope"></div></div>
    <h3>GROUP FUNCTIONAL TRAINING</h3>
    <p>The business is constantly staying<br>intouch with newest concepts by<br>upgrading the knowledge</p>
    <a>Read more &gt;&gt;</a>
  </div>
  <div class="service" style="left:614px">
    <div class="ring"><div role="img" aria-label="Icon of an athlete skating"></div></div>
    <h3>SPORTS PERFORMANCE</h3>
    <p>The business is constantly staying<br>intouch with newest concepts by<br>upgrading the knowledge</p>
    <a>Read more &gt;&gt;</a>
  </div>
  <div class="service" style="left:863px">
    <div class="ring"><div role="img" aria-label="Icon of a person in a pilates plank pose"></div></div>
    <h3>PILATES</h3>
    <p>The business is constantly staying<br>intouch with newest concepts by<br>upgrading the knowledge</p>
    <a>Read more &gt;&gt;</a>
  </div>
</section>

<div class="abs about-photo" role="img" aria-label="Portrait of the trainer in the garden"></div>
<section class="abs about">
  <h2><span class="accent">ABOUT FERN</span> FIT &amp; HEALTH</h2>
  <p>FERNFIT has trainers that have a Diploma of fitness from the Willow Institute&amp; are trained and qualified with the latest training techniques available anywhere in Australia, to give clients a better &amp; more reliable service with utting edge training programs and testing. The foundation of this business will be to service clients by functional training teniques and some machines, with a combination of group classes &amp; one on one Personal training. We also have an area for Pilates experience this is a very Japanese influenced setting &amp; is called, Organic Pilates experience.All my life I have been looking for a place that I can train in a comfortable and natural environment instead been surounded by concrete walls &amp; floors, what I am offering in my studio gym is a natural organic style of training that clients can feel whatit's like to be outside in the elements. This is something that you can come feel &amp; enjoy the pleasure of training in the outdoors and still accomplishing your goals.FERNFIT has trainers that have a Diploma of fitness from the Willow Institute&amp; are trained and qualified with the latest training techniques available anywhere in Australia</p>
  <span class="btn">View more info</span>
</section>

<section class="abs group">
  <h2>GROUP TRAINING SECTION</h2>
  <p>This area can accommodate 4-6 people at a time comfortably with a beautiful surrounding of a Japanese influenced garden. We have a combination of equip ment like Kettle Bells, Dumbbells, Battle ropes, Climbing wall, skipping ropes, hanging ropes, Olympic lifting bars, Tire flipping, Sled pulling,&amp; more.Group Training SectionThis area can accommodate 4-6 people at a time comfortably with a beautiful surrounding of a Japanese influenced garden. We have a combi-nation of equipment like Kettle Bells, Dumbbells, Battle ropes, Climbing wall, skipping ropes, hanging ropes.</p>
  <span class="btn">View more info</span>
  <div class="video">
    <div class="screen" role="img" aria-label="Video still of the timber deck training area with potted plants">
      <svg width="468" height="232" viewBox="0 0 468 232"><circle cx="234" cy="116" r="26" fill="#000" fill-opacity=".35" stroke="#fff" stroke-opacity=".7" stroke-width="2"/><path d="M226 102l20 14-20 14z" fill="#fff" fill-opacity=".8"/></svg>
    </div>
    <div class="bar">
      <svg width="10" height="10" viewBox="0 0 10 10"><path d="M1 0l8 5-8 5z" fill="#ddd"/></svg>
      <span>00:00/00:23</span>
      <span style="flex:1;height:4px;background:linear-gradient(90deg,#c8482e 60%,#555 60%)"></span>
      <svg width="12" height="10" viewBox="0 0 12 10"><path d="M0 3h3l4-3v10L3 7H0z" fill="#ddd"/></svg>
      <span style="width:60px;height:4px;background:#c8482e"></span>
    </div>
  </div>
</section>

<section class="testi">
  <h2><span class="accent">OUR</span> TESTIMONIALS</h2>
  <div class="abs testi-photo" role="img" aria-label="Portrait of a smiling client"></div>
  <span class="abs qmark" style="left:414px;top:2388px">“</span>
  <p class="abs quote">This area can accommodate 4-6 people at a time comfortably with a beautiful surrounding of a Japanese influenced garden. We have a combination of equip ment like Kettle Bells, Dumbbells, Battle ropes, Climb-ing wall, skipping ropes, hanging ropes...</p>
  <span class="abs qmark" style="left:1020px;top:2458px">”</span>
  <span class="abs testi-name">MAYA THORNTON</span>
  <span class="abs testi-role">Business man</span>
  <svg class="abs" style="left:1010px;top:2552px" width="28" height="12" viewBox="0 0 28 12"><circle cx="6" cy="6" r="5.5" fill="#cbcbcb"/><circle cx="22" cy="6" r="5.5" fill="#cbcbcb"/></svg>
</section>

<footer class="abs footer">
  <div class="abs brand"><span class="dot"></span><span>FERN FITNESS</span></div>
  <div class="abs hours" style="left:383px;top:38px">
    <h3>Trading hours</h3>
  </div>
  <div class="abs hours" style="left:383px;top:68px">
    <h4>April - September</h4>
    <ul><li>Monday – Friday 4.00pm - 6.00pm</li><li>Saturday- 12:00pm – 5:00pm</li><li>Sunday- 6:00am – 11:00am</li></ul>
  </div>
  <div class="abs hours" style="left:616px;top:68px">
    <h4>October – March</h4>
    <ul><li>Monday – Friday 4.00pm - 6.00pm</li><li>Saturday- 12:00pm – 5:00pm</li><li>Sunday- 6:00am – 11:00am</li></ul>
  </div>
  <div class="abs contact" style="left:878px;top:38px">
    <h3>Contact us</h3>
    <ul>
      <li><svg width="12" height="16" viewBox="0 0 12 16"><path d="M6 0a6 6 0 0 0-6 6c0 4.5 6 10 6 10s6-5.5 6-10a6 6 0 0 0-6-6zm0 8.3A2.3 2.3 0 1 1 6 3.7a2.3 2.3 0 0 1 0 4.6z" fill="#fff"/></svg><span>Studio Garden<br>14 Willow Lane</span></li>
      <li><svg width="14" height="14" viewBox="0 0 14 14"><path d="M1 2.5L4 1.5l1.8 4-2 1.5a9 9 0 0 0 3.8 3.8l1.5-2 4 1.8-1 3C6 14.5-.5 8 1 2.5z" fill="#fff"/></svg><span class="big">0400 123 456</span></li>
      <li style="margin-top:22px"><svg width="14" height="10" viewBox="0 0 14 10"><rect width="14" height="10" fill="#fff"/><path d="M0 0l7 6 7-6" fill="none" stroke="#2f2f2f" stroke-width="1.2"/></svg><span>hello@fernvitality.example</span></li>
    </ul>
  </div>
</footer>

<div class="abs bottom">
  <span class="abs" style="left:98px;top:17px">Copyright 2016 fernvitality. All Rights Reserved</span>
  <div class="social" style="left:1000px" aria-label="Social links"><span></span><span></span><span></span></div>
</div>

</body>
</html>
```